2021 Summer Ads Hollis Bay Custom Homes

We need a re-design of our summer ad run for our customer, Hollis Bay Custom Homes. They are custom home builders in the mostly rural parts of West Virginia, USA. They are known for their "Forever Home" tagline. We'd like two designed ads with the main difference being just the custom home that's featured. These designs should be for a Zintrola banner like 300 x 250 and square ad like 250 x 250. For inspiration please visit the Hollis Bay Custom Homes website at www dot hollisbaycustomhomes dot com

Target Market(s)

consumers / new home shoppers

Industry/Entity Type

Consumer

Requirements
Must have
• HBCH logo
Price Lock Available!
Custom home pic
Learn more >
small CFRM logo mark

```html
<!DOCTYPE html>
<html lang="en">
<head>
<meta charset="utf-8">
<title>Hollis Bay Custom Homes – Forever Home Ad</title>
<link href="https://fonts.googleapis.com/css2?family=Montserrat:wght@400;500;600;700;800&display=swap" rel="stylesheet">
<style>
  :root {
    --navy: #1d2530;
    --navy-light: #2b3440;
    --red: #d21f2b;
    --red-dark: #8e1219;
    --white: #ffffff;
    --photo-trees: #587f42;
    --photo-barn: #b5271f;
    --photo-ground: #d6c6a8;
  }
  html, body {
    margin: 0;
    padding: 0;
    width: 1200px;
    height: 1200px;
    overflow: hidden;
    background: var(--navy);
  }
  .ad {
    position: relative;
    width: 1200px;
    height: 1200px;
    overflow: hidden;
    font-family: "Montserrat", sans-serif;
    color: var(--white);
    background: linear-gradient(160deg, var(--navy-light) 0%, var(--navy) 60%);
  }
  .ad-shapes {
    position: absolute;
    inset: 0;
  }
  .brand {
    position: absolute;
    left: 60px;
    top: 48px;
    width: 400px;
    display: flex;
    align-items: center;
    gap: 22px;
  }
  .brand-square {
    width: 40px;
    height: 40px;
    background: var(--white);
    flex: none;
  }
  .brand-name {
    font-weight: 600;
    font-size: 40px;
    line-height: 1.1;
    letter-spacing: 1px;
    text-transform: uppercase;
  }
  .headline {
    position: absolute;
    left: 60px;
    top: 420px;
    margin: 0;
    text-transform: uppercase;
    font-size: 72px;
    line-height: 88px;
    letter-spacing: 1px;
  }
  .headline-light { display: block; font-weight: 400; }
  .headline-bold { display: block; font-weight: 800; }
  .offer {
    position: absolute;
    left: 60px;
    top: 832px;
    margin: 0;
    font-size: 46px;
    font-weight: 700;
    text-transform: uppercase;
    letter-spacing: 1px;
  }
  .cta {
    position: absolute;
    left: 60px;
    top: 948px;
    width: 420px;
    height: 135px;
    box-sizing: border-box;
    border: 4px solid var(--white);
    border-radius: 8px;
    display: flex;
    align-items: center;
    justify-content: center;
    font-size: 44px;
    font-weight: 600;
    letter-spacing: 2px;
    text-transform: uppercase;
    color: var(--white);
    text-decoration: none;
  }
</style>
</head>
<body>
<main class="ad">
  <svg class="ad-shapes" width="1200" height="1200" viewBox="0 0 1200 1200" xmlns="http://www.w3.org/2000/svg">
    <defs>
      <linearGradient id="home-photo-tones" x1="0" y1="0" x2="0.2" y2="1">
        <stop offset="0" stop-color="var(--photo-trees)"/>
        <stop offset="0.3" stop-color="var(--photo-barn)"/>
        <stop offset="0.62" stop-color="var(--photo-barn)"/>
        <stop offset="1" stop-color="var(--photo-ground)"/>
      </linearGradient>
    </defs>
    <polygon class="home-photo" role="img" aria-label="Photo of a red board-and-batten custom home with white trim and a cupola, surrounded by green trees"
             points="786,0 1200,0 1200,1200 960,1200 720,786" fill="url(#home-photo-tones)"/>
    <polygon class="accent-band" points="696,0 786,0 720,786 666,774" fill="var(--red)"/>
    <polygon class="accent-band-lower" points="666,774 720,786 990,1200 800,1200" fill="var(--red)"/>
    <polygon class="accent-band-shade" points="666,774 800,1200 700,1200" fill="var(--red-dark)"/>
    <rect class="partner-badge" x="735" y="1040" width="160" height="110" rx="10" fill="var(--white)"/>
  </svg>

  <div class="brand">
    <span class="brand-square"></span>
    <span class="brand-name">Hollis Bay Custom Homes</span>
  </div>

  <h1 class="headline">
    <span class="headline-light">Start</span>
    <span class="headline-light">Building</span>
    <span class="headline-bold">Your Forever</span>
    <span class="headline-bold">Home Today!</span>
  </h1>

  <p class="offer">Price Lock Available!</p>

  <a class="cta" href="#">Learn More</a>
</main>
</body>
</html>
```